Bespoke Builders Business Card Design

We need a business card for an established builder of high quality bespoke homes in Auckland and Northland. We build and renovate homes collaboratively facilitating effective communication between owners, builders, architects, suppliers and tradespeople. We have never built or renovated a home that leaks or has faults. We only use reliable materials. We have never been sued or had legal action taken against us. We are honest builders of bespoke homes not group mass produced homes. Our niche market is in character homes. We practice sustainability and have built a lot of coastal property. We have been in business for over thirty years . We would like to see natural colors of the environment sand,sea and maybe vegetation . The design should communicate quality, sustainability,fair pricing, open communication and the originality of bespoke building. And the fact that the builder is registered.

Industry/Entity Type

Business

Contact Information for Business Card

Rowan Tellick Builders
Ph. 021583917
18 Kestrel Rd Harwood Bay Auckland 0814
PO Box 927 Mangawhai 0583

```html
<!DOCTYPE html>
<html lang="en">
<head>
<meta charset="utf-8">
<title>Rowan Tellick Builders – Business Card</title>
<link rel="stylesheet" href="https://fonts.googleapis.com/css2?family=Old+Standard+TT:wght@700&family=Arimo:wght@400&display=swap">
<style>
  :root {
    --backdrop: #e4e2de;
    --navy: #1b1a4e;
    --navy-deep: #12113a;
    --paper: #ffffff;
    --paper-shade: #dcdcdc;
    --ink: #141414;
    --contact-text: #e6e6ee;
  }
  * { margin: 0; padding: 0; box-sizing: border-box; }
  html, body {
    width: 1200px;
    height: 892px;
    overflow: hidden;
    background: var(--backdrop);
  }
  .canvas {
    position: relative;
    width: 1200px;
    height: 892px;
  }
  .business-card {
    position: absolute;
    left: 120px;
    top: 146px;
    width: 960px;
    height: 600px;
    border-radius: 36px;
    overflow: hidden;
    background: linear-gradient(160deg, var(--navy) 0%, var(--navy-deep) 100%);
    box-shadow: 0 14px 30px rgba(0, 0, 0, 0.25);
  }
  .card-shapes {
    position: absolute;
    inset: 0;
    width: 100%;
    height: 100%;
  }
  .company-name {
    position: absolute;
    left: 0;
    width: 1000px;
    top: 196px;
    text-align: center;
    font-family: "Old Standard TT", "Century Schoolbook", serif;
    font-weight: 700;
    font-size: 56px;
    letter-spacing: 1px;
    color: var(--ink);
  }
  .contact-details {
    position: absolute;
    left: 150px;
    width: 800px;
    top: 418px;
    text-align: center;
    font-family: "Arimo", Arial, sans-serif;
    font-size: 25px;
    line-height: 1.55;
    color: var(--contact-text);
  }
  .contact-details .phone { margin-bottom: 14px; }
</style>
</head>
<body>
<main class="canvas">
  <article class="business-card">
    <svg class="card-shapes" viewBox="0 0 960 600" aria-hidden="true">
      <defs>
        <linearGradient id="paper-fill" x1="0" y1="0" x2="0.3" y2="1">
          <stop offset="0" stop-color="var(--paper)"/>
          <stop offset="1" stop-color="var(--paper-shade)"/>
        </linearGradient>
      </defs>
      <path class="paper-bowl" fill="url(#paper-fill)"
            d="M0,0 H960 V30 C880,330 560,400 330,372 C180,352 60,262 0,190 Z"/>
      <path class="swoosh-gap" fill="#ffffff"
            d="M0,190 C60,262 180,352 330,372 C560,400 880,330 960,30 V60 C860,360 560,420 330,392 C180,372 60,282 0,212 Z"/>
      <path class="swoosh" fill="var(--ink)"
            d="M0,200 C70,280 190,368 340,382 C500,394 620,366 730,315 C640,372 500,400 340,398 C190,394 80,318 0,232 Z"/>
    </svg>
    <h1 class="company-name">Rowan Tellick Builders</h1>
    <address class="contact-details" style="font-style: normal;">
      <p class="phone">021583917</p>
      <p class="street">18 Kestrel Rd Harwood Bay Auckland 0814</p>
      <p class="po-box">PO Box 927 Mangawhai 0583</p>
    </address>
  </article>
</main>
</body>
</html>
```